Need Business Card ASAP

We need a business card design for a meeting coming up in a few days. The company name is Harlow Ridge Building and Construction and the logo is attached. Something clean, cool, and contemporary that we can get to a printer right away. Attached is the business card for Volmar Energy, an affiliated company, which we like. Instead of the hawk on the back, you could use the attached "D". We'll also be needing matching letterhead in the near future, so ideas for that are welcome.

```html
<!DOCTYPE html>
<html lang="en">
<head>
<meta charset="utf-8">
<title>Harlow Ridge Building and Construction – Business Card</title>
<link href="https://fonts.googleapis.com/css2?family=Exo+2:wght@400;500;600&display=swap" rel="stylesheet">
<style>
  :root {
    --backdrop: #e9e7e2;
    --card: #ffffff;
    --gold: #b9b08a;
    --gold-light: #d6cfb0;
    --ink: #1d1b1c;
    --ink-soft: #3a3838;
  }
  html, body {
    margin: 0;
    width: 1200px;
    height: 876px;
    overflow: hidden;
    background: var(--backdrop);
    font-family: "Exo 2", sans-serif;
  }
  .canvas {
    position: relative;
    width: 1200px;
    height: 876px;
  }
  .card {
    position: absolute;
    left: 280px;
    width: 640px;
    height: 366px;
    background: var(--card);
    box-shadow: 0 6px 22px rgba(0,0,0,0.15);
    overflow: hidden;
  }
  .card--back { top: 44px; }
  .card--front { top: 466px; }

  .brand {
    position: absolute;
    display: flex;
    align-items: center;
    gap: 12px;
  }
  .brand__mark {
    flex: none;
    background: var(--gold);
  }
  .brand__name {
    color: var(--ink);
    font-weight: 500;
    line-height: 1.15;
    letter-spacing: 0.02em;
  }
  .card--back .brand {
    left: 50%;
    top: 50%;
    transform: translate(-50%, -50%);
    width: 330px;
  }
  .card--back .brand__mark { width: 78px; height: 78px; }
  .card--back .brand__name { font-size: 24px; }

  .card--front .brand {
    left: 38px;
    top: 30px;
    width: 240px;
  }
  .card--front .brand__mark { width: 52px; height: 52px; }
  .card--front .brand__name { font-size: 15px; }

  .stripes {
    position: absolute;
    left: 0;
    top: 0;
    width: 640px;
    height: 366px;
  }

  .person {
    position: absolute;
    right: 252px;
    top: 150px;
    text-align: right;
    color: var(--ink);
  }
  .person__name {
    margin: 0;
    font-size: 19px;
    font-weight: 500;
    letter-spacing: 0.06em;
  }
  .person__role {
    margin: 2px 0 0;
    font-size: 14px;
    letter-spacing: 0.05em;
    color: var(--ink-soft);
  }

  .contacts {
    position: absolute;
    left: 38px;
    top: 186px;
    margin: 0;
    padding: 0;
    list-style: none;
    color: var(--ink);
    font-size: 13.5px;
    letter-spacing: 0.03em;
  }
  .contacts li {
    display: flex;
    align-items: center;
    gap: 9px;
    height: 27px;
    white-space: nowrap;
  }
  .contacts svg { width: 15px; height: 15px; flex: none; }
</style>
</head>
<body>
<div class="canvas">

  <section class="card card--back" aria-label="Card back">
    <div class="brand">
      <span class="brand__mark"></span>
      <span class="brand__name">Harlow Ridge Building and Construction</span>
    </div>
  </section>

  <section class="card card--front" aria-label="Card front">
    <svg class="stripes" viewBox="0 0 640 366" aria-hidden="true">
      <polygon points="505,0 555,0 445,366 395,366" fill="var(--gold-light)"/>
      <polygon points="585,0 665,0 555,366 475,366" fill="var(--gold)"/>
      <polygon points="690,0 725,0 615,366 580,366" fill="var(--ink)"/>
    </svg>

    <div class="brand">
      <span class="brand__mark"></span>
      <span class="brand__name">Harlow Ridge Building and Construction</span>
    </div>

    <div class="person">
      <p class="person__name">JOHN SMITH</p>
      <p class="person__role">GENERAL MANAGER</p>
    </div>

    <ul class="contacts">
      <li>
        <svg viewBox="0 0 16 16" aria-hidden="true"><circle cx="8" cy="8" r="8" fill="var(--ink)"/><path d="M5.2 4.2l1.6-.4.8 2-1 .7a5 5 0 0 0 2.9 2.9l.7-1 2 .8-.4 1.6c-3.6.4-7-3-6.6-6.6z" fill="#fff"/></svg>
        041 872 3065
      </li>
      <li>
        <svg viewBox="0 0 16 16" aria-hidden="true"><circle cx="8" cy="8" r="8" fill="var(--ink)"/><rect x="5.6" y="3.6" width="4.8" height="8.8" rx="0.8" fill="#fff"/><rect x="6.4" y="4.8" width="3.2" height="5.6" fill="var(--ink)"/></svg>
        072 518 4490
      </li>
      <li>
        <svg viewBox="0 0 16 16" aria-hidden="true"><circle cx="8" cy="8" r="8" fill="var(--ink)"/><rect x="4" y="5.2" width="8" height="5.6" fill="#fff"/><path d="M4 5.2l4 3 4-3" stroke="var(--ink)" stroke-width="0.8" fill="none"/></svg>
        office@harlowridge.co
      </li>
      <li>
        <svg viewBox="0 0 16 16" aria-hidden="true"><circle cx="8" cy="8" r="8" fill="var(--ink)"/><g stroke="#fff" stroke-width="0.9" fill="none"><circle cx="8" cy="8" r="4.2"/><ellipse cx="8" cy="8" rx="1.8" ry="4.2"/><path d="M3.8 8h8.4"/></g></svg>
        www.harlowridge.co
      </li>
      <li>
        <svg viewBox="0 0 16 16" aria-hidden="true"><circle cx="8" cy="8" r="8" fill="var(--ink)"/><path d="M8 12.6s-3-3.3-3-5.4a3 3 0 0 1 6 0c0 2.1-3 5.4-3 5.4z" fill="#fff"/><circle cx="8" cy="7.2" r="1.1" fill="var(--ink)"/></svg>
        Suite 12, 4th Floor, Alder Court, Kestrel Road
      </li>
    </ul>
  </section>

</div>
</body>
</html>
```